Halvor Grading and Septic needs a flyer to submit to contractors to offer our services

I need a sleek profession one page full color high gloss document showcasing our services to give to Mobile Home Companies and contractors that need our services.

Target Market(s)

Home Builders. Mobile Home Salesmen. People Building new homes.

Industry/Entity Type

Construction

Font styles to use
Serif
Sans Serif

Requirements
Must have
• Phone Number. Email address. Logo. Services offered: Mobile Home Pads, Meter Pole Placement and Connection, Waterline Connection, On Site Septic System Installs
Should not have
• Jokes, Nothing trying to be cute

```html
<!DOCTYPE html>
<html lang="en">
<head>
<meta charset="utf-8">
<title>Halvor Grading and Septic – Services Flyer</title>
<link rel="stylesheet" href="https://fonts.googleapis.com/css2?family=Montserrat:wght@600;700&family=Poppins:ital,wght@1,400;1,500;1,700;1,800&display=swap">
<style>
  :root {
    --brand-blue: #15508a;
    --brand-red: #c9222b;
    --paper: #ffffff;
    --ring: #9aabc6;
    --page-bg: #666666;
    --photo-tone-a: #5a8fd6;
    --photo-tone-b: #86aee2;
  }
  html, body {
    margin: 0;
    padding: 0;
    width: 803px;
    height: 1200px;
    overflow: hidden;
    background: var(--page-bg);
  }
  .flyer {
    position: relative;
    width: 803px;
    height: 1200px;
    overflow: hidden;
    background: var(--brand-blue);
    color: var(--paper);
    font-family: "Poppins", Arial, sans-serif;
  }
  .flyer-shapes, .hero-photo {
    position: absolute;
    left: 0;
    top: 0;
    width: 803px;
    height: 1200px;
  }
  .brand-name {
    position: absolute;
    left: 44px;
    top: 44px;
    width: 260px;
    margin: 0;
    display: flex;
    align-items: center;
    gap: 12px;
    font-family: "Montserrat", Arial, sans-serif;
    font-weight: 700;
    font-size: 22px;
    line-height: 1.1;
    letter-spacing: 0.5px;
    color: var(--brand-blue);
    text-transform: uppercase;
  }
  .brand-mark {
    flex: 0 0 auto;
    width: 22px;
    height: 22px;
    background: var(--brand-blue);
  }
  .headline {
    position: absolute;
    left: 0;
    top: 488px;
    width: 803px;
    margin: 0;
    text-align: center;
    font-weight: 800;
    font-style: italic;
    font-size: 40px;
    line-height: 40px;
    letter-spacing: 0.5px;
    text-transform: uppercase;
  }
  .intro {
    position: absolute;
    left: 0;
    top: 588px;
    width: 803px;
    margin: 0;
    text-align: center;
    font-style: italic;
    font-weight: 500;
    font-size: 14.5px;
    line-height: 17px;
  }
  .cta {
    position: absolute;
    left: 0;
    top: 625px;
    width: 803px;
    margin: 0;
    text-align: center;
    font-style: italic;
    font-weight: 700;
    font-size: 21px;
  }
  .services-title {
    position: absolute;
    left: 69px;
    top: 678px;
    margin: 0;
    font-style: italic;
    font-weight: 700;
    font-size: 27px;
  }
  .service-list {
    list-style: none;
    margin: 0;
    padding: 0;
  }
  .service {
    position: absolute;
    left: 64px;
    display: flex;
    align-items: center;
    gap: 16px;
    height: 84px;
  }
  .service-icon {
    width: 84px;
    height: 84px;
    flex: 0 0 auto;
  }
  .service-name {
    font-family: "Montserrat", Arial, sans-serif;
    font-weight: 600;
    font-size: 26px;
    line-height: 26px;
    letter-spacing: 0.3px;
    text-transform: uppercase;
  }
  .contact {
    position: absolute;
    right: 40px;
    top: 1106px;
    margin: 0;
    text-align: right;
    font-style: normal;
  }
  .contact-phone {
    display: flex;
    justify-content: flex-end;
    align-items: center;
    gap: 10px;
    font-style: italic;
    font-weight: 800;
    font-size: 33px;
    line-height: 36px;
  }
  .contact-email {
    display: flex;
    justify-content: flex-end;
    align-items: center;
    gap: 8px;
    font-style: italic;
    font-weight: 500;
    font-size: 17px;
    line-height: 22px;
  }
</style>
</head>
<body>
<main class="flyer">

  <svg class="flyer-shapes" viewBox="0 0 803 1200" aria-hidden="true">
    <polygon points="0,0 803,0 803,200 0,200" fill="var(--paper)"/>
    <polygon points="0,150 338,150 366,30 803,30 803,48 380,48 352,168 0,168" fill="var(--brand-blue)"/>
    <polygon points="0,322 803,322 803,342 688,345 656,470 76,470 28,345 0,340" fill="var(--brand-red)"/>
    <polygon points="0,160 350,160 377,56 803,56 803,336 682,336 650,440 114,440 102,336 0,336" fill="var(--paper)"/>
    <polygon points="0,1188 290,1188 285,1200 0,1200" fill="var(--paper)"/>
    <polygon points="296,1090 803,1090 803,1200 270,1200" fill="var(--paper)"/>
    <polygon points="308,1098 803,1098 803,1200 284,1200" fill="var(--brand-red)"/>
  </svg>

  <svg class="hero-photo" viewBox="0 0 803 1200" role="img" aria-label="Photo: precast concrete septic tank being lowered by a crane boom onto a dug site">
    <defs>
      <linearGradient id="hero-tones" x1="0" y1="0" x2="0" y2="1">
        <stop offset="0" stop-color="var(--photo-tone-a)"/>
        <stop offset="1" stop-color="var(--photo-tone-b)"/>
      </linearGradient>
    </defs>
    <polygon points="0,166 354,166 381,62 803,62 803,330 678,330 646,432 120,432 108,330 0,330" fill="url(#hero-tones)"/>
  </svg>

  <p class="brand-name"><span class="brand-mark"></span>Halvor Grading &amp; Septic</p>

  <h1 class="headline">Professional Wastewater<br>Management</h1>
  <p class="intro">Halvor Grading and Septic offers professional septic and<br>excavation services in East Texas.</p>
  <p class="cta">Call us now for a free estimate!</p>

  <h2 class="services-title">Services offered:</h2>
  <ul class="service-list">
    <li class="service" style="top:737px">
      <svg class="service-icon" viewBox="0 0 84 84" aria-hidden="true">
        <circle cx="42" cy="42" r="40" fill="var(--ring)"/>
        <circle cx="42" cy="42" r="34" fill="var(--brand-red)"/>
        <rect x="25" y="30" width="34" height="20" fill="none" stroke="#fff" stroke-width="3"/>
        <polyline points="23,32 42,20 61,32" fill="none" stroke="#fff" stroke-width="3"/>
        <circle cx="32" cy="55" r="3" fill="none" stroke="#fff" stroke-width="2"/>
        <circle cx="41" cy="55" r="3" fill="none" stroke="#fff" stroke-width="2"/>
      </svg>
      <span class="service-name">Mobile Home Pads</span>
    </li>
    <li class="service" style="top:827px">
      <svg class="service-icon" viewBox="0 0 84 84" aria-hidden="true">
        <circle cx="42" cy="42" r="40" fill="var(--ring)"/>
        <circle cx="42" cy="42" r="34" fill="var(--brand-red)"/>
        <line x1="32" y1="22" x2="32" y2="60" stroke="#fff" stroke-width="3"/>
        <line x1="22" y1="28" x2="42" y2="28" stroke="#fff" stroke-width="3"/>
        <rect x="44" y="42" width="16" height="14" fill="none" stroke="#fff" stroke-width="3"/>
      </svg>
      <span class="service-name">Meter Pole Placement<br>and Connection</span>
    </li>
    <li class="service" style="top:922px">
      <svg class="service-icon" viewBox="0 0 84 84" aria-hidden="true">
        <circle cx="42" cy="42" r="40" fill="var(--ring)"/>
        <circle cx="42" cy="42" r="34" fill="var(--brand-red)"/>
        <path d="M26 28 H46 V46 H58" fill="none" stroke="#fff" stroke-width="6"/>
        <path d="M34 46 V60" fill="none" stroke="#fff" stroke-width="6"/>
      </svg>
      <span class="service-name">Waterline Connection</span>
    </li>
    <li class="service" style="top:1014px">
      <svg class="service-icon" viewBox="0 0 84 84" aria-hidden="true">
        <circle cx="42" cy="42" r="40" fill="var(--ring)"/>
        <circle cx="42" cy="42" r="34" fill="var(--brand-red)"/>
        <rect x="26" y="34" width="32" height="24" fill="#fff"/>
        <rect x="30" y="24" width="8" height="10" fill="#fff"/>
        <rect x="46" y="24" width="8" height="10" fill="#fff"/>
      </svg>
      <span class="service-name">On Site Septic System Installs</span>
    </li>
  </ul>

  <address class="contact">
    <div class="contact-phone">
      <svg width="24" height="24" viewBox="0 0 24 24" aria-hidden="true">
        <path d="M6.6 10.8a15 15 0 0 0 6.6 6.6l2.2-2.2a1 1 0 0 1 1-.25 11.4 11.4 0 0 0 3.6.57 1 1 0 0 1 1 1V20a1 1 0 0 1-1 1A17 17 0 0 1 3 4a1 1 0 0 1 1-1h3.5a1 1 0 0 1 1 1c0 1.25.2 2.45.57 3.57a1 1 0 0 1-.25 1z" fill="#fff"/>
      </svg>
      <span>(555) 214-0678</span>
    </div>
    <div class="contact-email">
      <svg width="18" height="18" viewBox="0 0 18 18" aria-hidden="true">
        <circle cx="9" cy="9" r="9" fill="#fff"/>
        <rect x="4" y="5.5" width="10" height="7" fill="none" stroke="var(--brand-red)" stroke-width="1.4"/>
        <polyline points="4,5.5 9,9.5 14,5.5" fill="none" stroke="var(--brand-red)" stroke-width="1.4"/>
      </svg>
      <span>office@halvorgradingandseptic.com</span>
    </div>
  </address>

</main>
</body>
</html>
```